Velk Partners Building Business Cards

We need a business card that reflects our business as "Solar Experts" in San Diego. Browse our website www.velkpartners.example our License needs to be displayed as "CSLB# 3867140" our phone number is (619) 555-0187

Save thousands on your electric bills and increase the value of your home while helping to protect the environment. Our solar installation experts will help you design the system that's right for you, using only the highest quality equipment that will look great and give you ideal performance. Our goal is to make you energy independent, and get your electric bill to 0.

Paul Osterby
(619) 555-0187
paul@velkpartners.example

Target Market(s)

Home owners in san diego looking for solar

Industry/Entity Type

Solar Energy

Contact Information for Business Card

Paul Osterby
(619) 555-0187
paul@velkpartners.example

Font styles to use
Other font styles liked:
• Use our logo font

Requirements
Must have
• License needs to be displayed as "CSLB# 3867140" our phone number is (619) 555-0187
Nice to have
• Real images of rooftop home solar in san diego
Should not have
• our business address

```html
<!DOCTYPE html>
<html lang="en">
<head>
<meta charset="utf-8">
<title>Velk Partners Building – Business Cards</title>
<link rel="stylesheet" href="https://fonts.googleapis.com/css2?family=Roboto:wght@400;500;700&display=swap">
<style>
  :root {
    --navy: #24427f;
    --navy-deep: #1f3a72;
    --blue-front: #2c4c96;
    --gold: #e9a514;
    --paper: #fbfbfa;
    --backdrop: #9e9b9b;
    --ink-soft: #2b3e6b;
  }
  * { box-sizing: border-box; margin: 0; padding: 0; }
  html, body { width: 1200px; height: 1200px; overflow: hidden; }
  body {
    background: var(--backdrop);
    font-family: "Roboto", Arial, sans-serif;
    position: relative;
  }
  .card {
    position: absolute;
    left: 244px;
    width: 712px;
    height: 418px;
    border-radius: 24px;
    overflow: hidden;
  }
  /* Front */
  .card-front { top: 118px; background: var(--blue-front); }
  .front-photo {
    position: absolute; inset: 0;
    background: linear-gradient(160deg, #34549d 0%, #2b4a93 45%, #27468c 100%);
  }
  .front-name {
    position: absolute; left: 0; right: 0; top: 150px;
    text-align: center; color: #fff;
    font-weight: 700; font-size: 50px; letter-spacing: -0.5px;
  }
  .front-license {
    position: absolute; left: 0; right: 0; top: 364px;
    display: flex; justify-content: center; align-items: center; gap: 20px;
    color: #fff; font-size: 17px;
  }
  .front-license .dash { width: 54px; height: 3px; background: var(--gold); }
  /* Back */
  .card-back { top: 645px; background: var(--paper); }
  .holder { position: absolute; left: 25px; top: 64px; color: var(--navy); }
  .holder-name { font-weight: 700; font-size: 25px; }
  .holder-title { font-size: 16px; margin-top: 6px; color: var(--ink-soft); }
  .back-name {
    position: absolute; right: 34px; top: 52px; width: 360px;
    text-align: right; color: var(--navy);
    font-weight: 700; font-size: 38px; line-height: 1.05; letter-spacing: -0.5px;
  }
  .contacts { position: absolute; left: 26px; top: 228px; list-style: none; }
  .contacts li {
    display: flex; align-items: center; gap: 16px;
    font-size: 18px; color: var(--navy); height: 25px;
  }
  .contacts svg { width: 18px; height: 16px; fill: var(--gold); }
  .contacts .accent { color: var(--gold); }
  .wave { position: absolute; left: 0; top: 0; width: 712px; height: 418px; }
  .back-license {
    position: absolute; right: 34px; top: 346px;
    color: #fff; font-size: 17px;
  }
</style>
</head>
<body>
  <section class="card card-front">
    <div class="front-photo" role="img" aria-label="Faded photo of rooftop solar panels in blue tones"></div>
    <div class="front-name">Velk Partners Building</div>
    <div class="front-license"><span class="dash"></span><span>License: CSLB# 3867140</span><span class="dash"></span></div>
  </section>

  <section class="card card-back">
    <svg class="wave" viewBox="0 0 712 418" aria-hidden="true">
      <path d="M0,372 C160,402 330,392 455,330 C560,276 630,236 712,232 L712,418 L0,418 Z" fill="var(--navy-deep)"/>
      <path d="M0,328 C120,372 300,380 430,318 C540,266 620,212 712,202 L712,216 C630,222 560,262 455,312 C330,372 150,372 0,344 Z" fill="var(--gold)"/>
      <path d="M60,338 C200,368 310,360 380,338 C300,372 170,370 60,338 Z" fill="var(--gold)"/>
    </svg>
    <div class="holder">
      <div class="holder-name">Paul Osterby</div>
      <div class="holder-title">Managing Director</div>
    </div>
    <div class="back-name">Velk Partners Building</div>
    <ul class="contacts">
      <li><svg viewBox="0 0 18 16"><path d="M2 5c0-2 3-3 7-3s7 1 7 3v2h-4V5H6v2H2z M4 8h10l2 6H2z"/></svg>(619) 555-0187</li>
      <li><svg viewBox="0 0 18 16"><circle cx="9" cy="8" r="7"/><path d="M2 8h14M9 1v14" stroke="#fff" stroke-width="1.2"/></svg>paul@velkpartners.example</li>
      <li><svg viewBox="0 0 18 16"><path d="M1 3h16v10H1z"/><path d="M1 3l8 6 8-6" stroke="#fff" stroke-width="1.3" fill="none"/></svg>www.<span class="accent">velkpartners</span>.example</li>
    </ul>
    <div class="back-license">License: CSLB# 3867140</div>
  </section>
</body>
</html>
```